Landing Page and Logo for Auto-Blogging Platform

I created a platform that allows users to start a blog for their business, hobby, charity, etc. I need a landing page where users can learn about the platform, benefits of consistent blogging, SEO value, plans/pricing, etc. The landing page needs to have multiple call to action buttons encouraging the visitor to register/sign up for a free trial.

In addition to the landing page, I need a page for users to establish the settings for their blog. This page should be a fairly simple form, intended for the user to enter a few details to set up their blog:
1. Name of Blog
2. Up to 10 topics and/or keywords the blog should focus on
3. Theme: Color-scheme and logo upload for blog.

I have attached the specifications of the platform's functionality so you can better understand how it works, plans/pricing, etc.

I also need a logo for the business. The name of the platform is PostNook.

Target Market(s)

Website owners, bloggers, business owners

Industry/Entity Type

Technology, Internet, web design

Coding

Coded - Design and coding required

Number of Pages Required

2 page

Colors
0054AA
0677BA
7BADD7
CADEEF
E8F1F8
0094D4
00A9DD
6FCCEA
C7EBF8
E9F6FB

Requirements
Must have
• Eye-catching design but fairly light on content (keep it simple and brief.)
Nice to have
• Eye-catching yet simple design, clean and easy to understand what we are offering.
Should not have
• Too much “wordy” and confusing content.

```html
<!DOCTYPE html>
<html lang="en">
<head>
<meta charset="UTF-8">
<title>PostNook — Automate Your Blog Posting with AI</title>
<link rel="stylesheet" href="https://fonts.googleapis.com/css2?family=Manrope:wght@500;600;700;800&family=Inter:wght@400;500;600&display=swap">
<style>
  :root{
    --blue-deep:#0054AA;
    --blue:#0677BA;
    --blue-bright:#1f6fe0;
    --blue-soft:#7BADD7;
    --blue-pale:#CADEEF;
    --blue-mist:#E8F1F8;
    --sky:#00A9DD;
    --ink:#1d2433;
    --ink-soft:#5b6475;
    --line:#e6e9ef;
    --panel:#ffffff;
    --bg:#f4f6f9;
    --lime:#c8e63c;
  }
  *{box-sizing:border-box;margin:0;padding:0}
  html,body{width:1200px;height:800px;overflow:hidden}
  body{background:var(--bg);font-family:"Inter",sans-serif;color:var(--ink)}
  .page{position:relative;width:1200px;height:800px;overflow:hidden;background:#fff}

  /* navigation */
  .nav{height:66px;display:flex;align-items:center;padding:0 48px;border-bottom:1px solid var(--line);background:#fff;position:relative;z-index:2}
  .brand{display:flex;align-items:center;gap:8px;font-family:"Manrope",sans-serif;font-weight:800;font-size:20px;color:var(--blue-deep)}
  .brand-mark{width:14px;height:14px;border-radius:3px;background:var(--blue-deep)}
  .nav-links{display:flex;gap:22px;margin-left:auto;margin-right:auto;font-size:13px;color:var(--ink)}
  .nav-actions{display:flex;gap:10px}
  .btn{font-family:"Inter",sans-serif;font-size:12.5px;border-radius:5px;padding:8px 14px;display:inline-flex;align-items:center;gap:6px}
  .btn-outline{border:1px solid #b9c0cc;color:var(--ink);background:#fff}
  .btn-primary{background:var(--blue-bright);color:#fff;border:1px solid var(--blue-bright)}

  /* hero */
  .hero{position:relative;height:734px;background:
      linear-gradient(#fff 0,rgba(255,255,255,0) 40%),
      repeating-linear-gradient(90deg,transparent 0 79px,#eef1f5 79px 80px),
      repeating-linear-gradient(0deg,transparent 0 79px,#eef1f5 79px 80px),#fafbfc;
      text-align:center;padding-top:64px}
  .eyebrow{font-size:12px;font-weight:600;color:var(--blue-bright)}
  .headline{font-family:"Manrope",sans-serif;font-weight:800;font-size:54px;line-height:1.05;margin-top:14px;
    background:linear-gradient(180deg,var(--blue-deep) 0%,var(--blue-bright) 55%,var(--blue-soft) 100%);
    -webkit-background-clip:text;background-clip:text;color:transparent}
  .lede{font-size:14px;line-height:1.6;color:var(--ink-soft);margin:18px auto 0;width:460px}
  .hero-ctas{display:flex;justify-content:center;gap:10px;margin-top:20px}
  .hero-ctas .btn{padding:10px 16px}

  /* dashboard preview */
  .dash{position:absolute;left:100px;top:372px;width:1000px;height:420px;background:var(--panel);border:1px solid var(--line);border-radius:8px 8px 0 0;display:flex;text-align:left;box-shadow:0 20px 40px rgba(20,40,80,.08);overflow:hidden}
  .rail{width:48px;border-right:1px solid var(--line);display:flex;flex-direction:column;align-items:center;gap:22px;padding-top:16px}
  .rail-icon{width:20px;height:20px;border-radius:5px;border:1.5px solid #9aa3b2}
  .rail-icon.active{background:var(--blue-bright);border-color:var(--blue-bright)}
  .projects{width:170px;border-right:1px solid var(--line);padding:14px 12px;font-size:11px}
  .search{border:1px solid var(--line);border-radius:5px;padding:7px 8px;color:#a2a9b6;font-size:10px}
  .projects h4{font-size:11px;font-weight:600;margin:18px 0 10px;display:flex;justify-content:space-between}
  .project{padding:11px 12px;border:1px solid var(--line);border-radius:5px;margin-bottom:8px;font-weight:500}
  .project.current{background:var(--blue-bright);color:#fff;border-color:var(--blue-bright)}
  .main{flex:1;padding:14px 18px}
  .main-head{display:flex;align-items:center;gap:10px}
  .ws-mark{width:30px;height:30px;border-radius:50%;background:var(--lime)}
  .ws-name{font-family:"Manrope",sans-serif;font-weight:700;font-size:14px}
  .ws-sub{font-size:10px;color:var(--ink-soft)}
  .head-tools{margin-left:auto;display:flex;gap:14px;align-items:center}
  .tool{width:14px;height:14px;border:1.5px solid #6b7383;border-radius:50%}
  .avatars{display:flex;margin-left:14px}
  .avatar{width:22px;height:22px;border-radius:50%;border:2px solid #fff;margin-left:-6px;background:#c9b8a6}
  .avatar:nth-child(2){background:#8a9bb0}.avatar:nth-child(3){background:#d8a98b}.avatar:nth-child(4){background:#6e7f91}
  .avatar.count{background:#2e9d5b}
  .tabs{display:flex;gap:18px;font-size:10.5px;color:var(--ink-soft);margin-top:14px;border-bottom:1px solid var(--line);padding-bottom:8px}
  .tabs .on{color:var(--ink);font-weight:600}
  .dot{display:inline-block;width:7px;height:7px;border-radius:50%;background:#e5484d;margin-left:4px}
  .views{display:flex;gap:8px;align-items:center;margin-top:12px;font-size:10.5px;color:var(--ink-soft)}
  .view{padding:6px 10px;border-radius:4px}
  .view.on{background:var(--blue-bright);color:#fff}
  .views .right{margin-left:auto;display:flex;gap:10px}
  .views .right span{border:1px solid var(--line);padding:6px 12px;border-radius:4px}
  .group{margin-top:16px;border:1px solid var(--line);border-radius:6px;padding:12px}
  .group-title{font-size:11px;font-weight:500;display:flex;justify-content:space-between}
  .table{margin-top:14px;font-size:10.5px}
  .row{display:grid;grid-template-columns:2.2fr 1fr 1fr 1fr .8fr;padding:10px 6px;align-items:center}
  .row.head{color:var(--ink-soft);border-bottom:1px solid var(--line)}
  .flag{width:10px;height:12px;display:block}
  .cell-dot{width:10px;height:10px;border-radius:50%;background:#7a8595}
  .pair{display:flex}.pair .avatar{width:20px;height:20px}
</style>
</head>
<body>
<div class="page">
  <header class="nav">
    <div class="brand"><span class="brand-mark"></span>PostNook</div>
    <nav class="nav-links"><span>About</span><span>Features</span><span>How it Works</span><span>Pricing</span><span>Faqs</span></nav>
    <div class="nav-actions"><span class="btn btn-outline">Sign in</span><span class="btn btn-primary">Start for free</span></div>
  </header>

  <section class="hero">
    <p class="eyebrow">One Platform for all your Content</p>
    <h1 class="headline">Automate Your Blog<br>Posting with AI</h1>
    <p class="lede">Improving SEO results by constantly automate posting fresh, new, keyword-targeted content to your website or blog.</p>
    <div class="hero-ctas">
      <span class="btn btn-primary">Get Started Now</span>
      <span class="btn btn-outline">
        <svg width="9" height="10" viewBox="0 0 9 10"><path d="M1 1l7 4-7 4z" fill="none" stroke="#1d2433" stroke-width="1.3"/></svg>
        Watch the Demo</span>
    </div>

    <div class="dash">
      <div class="rail">
        <span class="rail-icon active"></span><span class="rail-icon"></span><span class="rail-icon"></span>
        <span class="rail-icon"></span><span class="rail-icon"></span><span class="rail-icon"></span>
      </div>
      <aside class="projects">
        <div class="search">Search for a project</div>
        <h4>My Blog Articles <span>⌃</span></h4>
        <div class="project">Maple Art</div>
        <div class="project current">Handy Bags</div>
        <div class="project">Stylish Hats</div>
        <div class="project">New Maple Tools</div>
      </aside>
      <div class="main">
        <div class="main-head">
          <span class="ws-mark"></span>
          <div><div class="ws-name">Maple Works</div><div class="ws-sub">Website Blog Articles</div></div>
          <div class="head-tools"><span class="tool"></span><span class="tool"></span><span class="tool"></span><span class="tool"></span>
            <div class="avatars"><span class="avatar"></span><span class="avatar"></span><span class="avatar"></span><span class="avatar"></span><span class="avatar count"></span></div>
          </div>
        </div>
        <div class="tabs"><span>Overview</span><span class="on">Blog</span><span>Discussions<i class="dot"></i></span><span>Team Members</span><span>Notifications<i class="dot"></i></span><span>Files</span><span>Integrations</span></div>
        <div class="views">
          <span class="view">Board View</span><span class="view on">List View</span><span class="view">Timeline View</span>
          <div class="right"><span>Sort By</span><span>Filter</span></div>
        </div>
        <div class="group">
          <div class="group-title"><span>Open (08)</span><span>+ ⋮</span></div>
          <div class="table">
            <div class="row head"><span>Task Name</span><span>Assigned to</span><span>Due Date</span><span>Tags</span><span>Priority</span></div>
            <div class="row">
              <span>Prepare high-fidelity wireframe landing</span>
              <span class="pair"><span class="avatar"></span><span class="avatar"></span></span>
              <span class="cell-dot"></span><span class="cell-dot"></span>
              <svg class="flag" viewBox="0 0 10 12"><path d="M1 0v12M1 1h7l-2 3 2 3H1" fill="none" stroke="#7a8595" stroke-width="1.2"/></svg>
            </div>
          </div>
        </div>
      </div>
    </div>
  </section>
</div>
</body>
</html>
```